Spring Detox sale graphics for social media

You MUST read the Brief in the WORD document and follow the instructions there. I want to create 10 social media graphics (new Instagram size 4:5 (1080 x 1350 pixels) focusing on our Mother’s Day Spring Detox Sale graphics, using any of the pics attached. Use the attached pics, NO RANDOM STOCK PHOTOGRAPHY. For the color scheme of the graphics, they should all be complementary to the product colors or feel like Spring time.

Target Market(s)

primarily women

Requirements
Must have
• the photos and text attached

```html
<!DOCTYPE html>
<html lang="en">
<head>
<meta charset="utf-8">
<title>Mother's Day Spring Detox Sale – Social Set</title>
<link rel="stylesheet" href="https://fonts.googleapis.com/css2?family=Anton&family=Archivo+Black&family=Montserrat:wght@700;800&family=Oswald:wght@500;600;700&display=swap">
<style>
:root{
  --canvas:#555555;
  --white:#ffffff;
  --forest:#1f4a3d;
  --leaf:#a3cc7f;
  --rose:#d46ea2;
  --orchid:#a64886;
  --plum:#7d2f68;
  --blush:#ee9cbf;
}
*{margin:0;padding:0;box-sizing:border-box}
html,body{width:1200px;height:3484px;overflow:hidden;background:var(--canvas)}
.sheet{position:relative;width:1200px;height:3484px;background:var(--canvas)}
.post{position:absolute;width:494px;height:617px;background:var(--white);overflow:hidden}
.col-a{left:88px}.col-b{left:630px}
.row-1{top:107px}.row-2{top:766px}.row-3{top:1425px}.row-4{top:2083px}.row-5{top:2742px}
.t{position:absolute;left:0;right:0;text-align:center;line-height:1;white-space:nowrap}
.cond{font-family:"Oswald",sans-serif;font-weight:700;letter-spacing:-1px}
.anton{font-family:"Anton",sans-serif}
.wide{font-family:"Archivo Black",sans-serif}
.sans{font-family:"Montserrat",sans-serif;font-weight:800}
.shape{position:absolute;left:0;top:0;width:494px;height:617px}
.bottles{position:absolute;border-radius:14px;background:linear-gradient(180deg,#f4f4f4 0%,#e2e2e2 55%,#c9b6cc 78%,#9fb8c9 100%)}
.pct{position:absolute;line-height:1;white-space:nowrap}
.pct-group{position:absolute;display:flex;align-items:flex-end;white-space:nowrap}
.pct-num{line-height:.78}
.pct-stack{display:flex;flex-direction:column;align-items:center;line-height:.82}
.vertical{position:absolute;writing-mode:vertical-rl;transform:rotate(180deg);white-space:nowrap;line-height:.9}
.rule{position:absolute;height:2px}
.green-txt{color:var(--leaf)}.forest-txt{color:var(--forest)}.rose-txt{color:var(--rose)}.orchid-txt{color:var(--orchid)}.plum-txt{color:var(--plum)}.white-txt{color:var(--white)}
.portrait{position:absolute;left:210px;top:40px;width:284px;height:577px;background:radial-gradient(ellipse at 55% 40%,#c9a48f 0%,#b78b78 30%,#e9d9d6 62%,rgba(238,156,191,0) 85%)}
</style>
</head>
<body>
<main class="sheet">

<!-- 1 -->
<section class="post col-a row-1">
  <svg class="shape" viewBox="0 0 494 617"><polygon points="12,617 494,617 494,502" fill="#a3cc7f"/></svg>
  <div class="t sans forest-txt" style="top:50px;font-size:54px;font-weight:700">Mother’s Day</div>
  <div class="t anton green-txt" style="top:128px;font-size:84px">SPRING DETOX</div>
  <div class="t wide forest-txt" style="top:222px;font-size:90px">SALE</div>
  <div class="t wide green-txt" style="top:322px;font-size:52px">25% OFF</div>
  <div class="bottles" role="img" aria-label="Four supplement bottles" style="left:112px;top:392px;width:350px;height:138px"></div>
  <div class="t anton forest-txt" style="top:536px;left:118px;right:30px;font-size:70px">EVERYTHING!</div>
</section>

<!-- 2 -->
<section class="post col-b row-1">
  <div class="t wide forest-txt" style="top:30px;font-size:66px">25% OFF</div>
  <div style="position:absolute;left:33px;top:110px;width:426px;height:50px;background:var(--leaf)"></div>
  <div class="t wide forest-txt" style="top:115px;font-size:40px">MOTHER’S DAY</div>
  <div class="t anton green-txt" style="top:170px;font-size:142px">SPRING</div>
  <div class="t anton green-txt" style="top:300px;font-size:162px">DETOX</div>
  <div class="t anton forest-txt" style="top:470px;left:60px;text-align:left;font-size:96px">SALE</div>
  <div class="bottles" role="img" aria-label="Four supplement bottles" style="left:236px;top:475px;width:237px;height:122px"></div>
  <div style="position:absolute;left:0;bottom:0;width:494px;height:20px;background:var(--leaf)"></div>
</section>

<!-- 3 -->
<section class="post col-a row-2">
  <svg class="shape" viewBox="0 0 494 617"><polygon points="0,525 494,491 494,617 0,617" fill="#1f4a3d"/></svg>
  <div class="t anton green-txt" style="top:30px;font-size:86px">SPRING DETOX</div>
  <div class="t anton forest-txt" style="top:130px;font-size:84px">SALE!</div>
  <div class="pct-group green-txt" style="left:110px;top:248px">
    <span class="wide pct-num" style="font-size:150px">25</span>
    <span class="pct-stack" style="margin-left:-6px">
      <span class="wide" style="font-size:72px">%</span>
      <span class="cond" style="font-size:54px">OFF</span>
    </span>
  </div>
  <div class="bottles" role="img" aria-label="Four supplement bottles" style="left:65px;top:382px;width:365px;height:131px"></div>
  <div class="t anton white-txt" style="top:540px;font-size:66px">ALL SUPPLEMENTS</div>
</section>

<!-- 4 -->
<section class="post col-b row-2">
  <div class="pct-group rose-txt" style="left:58px;top:26px">
    <span class="wide pct-num" style="font-size:150px">25</span>
    <span class="pct-stack" style="margin-left:-6px">
      <span class="wide" style="font-size:74px">%</span>
      <span class="cond" style="font-size:56px">OFF</span>
    </span>
  </div>
  <div class="rule" style="left:6px;top:181px;width:60px;background:var(--orchid)"></div>
  <div class="rule" style="left:428px;top:181px;width:60px;background:var(--orchid)"></div>
  <div class="t anton orchid-txt" style="top:158px;font-size:44px">SPRING DETOX SALE</div>
  <div class="t wide rose-txt" style="top:212px;font-size:90px">SPRING</div>
  <div class="t wide rose-txt" style="top:306px;font-size:90px">RESET</div>
  <div style="position:absolute;left:0;top:492px;width:494px;height:125px;background:var(--orchid)"></div>
  <div class="bottles" role="img" aria-label="Four supplement bottles" style="left:110px;top:400px;width:290px;height:140px"></div>
  <div class="t wide white-txt" style="top:556px;font-size:42px">SUMMER READY</div>
</section>

<!-- 5 -->
<section class="post col-a row-3">
  <svg class="shape" viewBox="0 0 494 617">
    <polygon points="0,0 120,0 300,100 0,205" fill="#a64886"/>
    <polygon points="494,250 494,370 440,377 440,300" fill="#7d2f68"/>
  </svg>
  <div class="bottles" role="img" aria-label="Four supplement bottles" style="left:15px;top:60px;width:262px;height:105px"></div>
  <div class="pct-group plum-txt" style="left:286px;top:58px">
    <span class="cond pct-num" style="font-size:130px;font-weight:600">25</span>
    <span class="pct-stack" style="margin-left:2px">
      <span class="cond" style="font-size:66px;font-weight:500">%</span>
      <span class="cond" style="font-size:46px;font-weight:500">OFF</span>
    </span>
  </div>
  <div class="t wide rose-txt" style="top:208px;font-size:57px">EVERYTHING</div>
  <div style="position:absolute;left:30px;top:291px;width:412px;height:84px;background:var(--plum)"></div>
  <div class="t anton white-txt" style="top:290px;left:30px;right:52px;font-size:72px">MOTHER’S DAY</div>
  <div class="t anton rose-txt" style="top:386px;font-size:92px">SPRING</div>
  <div class="rule" style="left:0;top:534px;width:38px;background:var(--rose)"></div>
  <div class="rule" style="left:456px;top:534px;width:38px;background:var(--rose)"></div>
  <div class="t anton rose-txt" style="top:490px;font-size:92px">DETOX SALE</div>
</section>

<!-- 6 -->
<section class="post col-b row-3">
  <svg class="shape" viewBox="0 0 494 617">
    <polygon points="0,400 32,455 32,581 0,540" fill="#a3cc7f"/>
    <polygon points="494,400 459,455 459,581 494,540" fill="#a3cc7f"/>
  </svg>
  <div class="t anton green-txt" style="top:36px;font-size:82px">MOTHER’S DAY</div>
  <div class="t anton forest-txt" style="top:112px;font-size:118px">SALE</div>
  <div class="t wide green-txt" style="top:240px;font-size:78px">25% OFF</div>
  <div class="bottles" role="img" aria-label="Four supplement bottles" style="left:85px;top:327px;width:325px;height:128px"></div>
  <div style="position:absolute;left:32px;top:455px;width:427px;height:126px;background:var(--forest)"></div>
  <div class="t wide white-txt" style="top:466px;font-size:42px;font-style:italic;line-height:1.3">FEEL AMAZING<br>AGAIN!</div>
</section>

<!-- 7 -->
<section class="post col-a row-4" style="background:linear-gradient(100deg,#ef88b3 0%,#f0a3c4 55%,#e9cbd6 100%)">
  <div class="portrait" role="img" aria-label="Smiling woman in a white knit top standing behind a counter with supplement bottles"></div>
  <div class="t wide white-txt" style="left:26px;text-align:left;top:18px;font-size:70px;line-height:1.2">REFRESH<br>YOUR<br>BODY</div>
  <div class="t sans white-txt" style="left:24px;text-align:left;top:302px;font-size:56px;font-weight:700;line-height:1.2">25% Off<br>Mother’s<br>Day<br>Sale</div>
</section>

<!-- 8 -->
<section class="post col-b row-4">
  <div class="t wide plum-txt" style="top:38px;font-size:60px">25% OFF</div>
  <div class="t anton orchid-txt" style="top:116px;font-size:62px">SPRING DETOX SALE</div>
  <div class="rule" style="left:36px;top:209px;width:422px;background:var(--orchid)"></div>
  <div class="t wide orchid-txt" style="top:234px;font-size:100px">SPRING</div>
  <div class="t wide orchid-txt" style="top:340px;font-size:88px">CLEANSE</div>
  <div class="rule" style="left:36px;top:466px;width:422px;background:var(--orchid)"></div>
  <div class="t anton rose-txt" style="top:488px;font-size:76px">SUMMER GLOW</div>
</section>

<!-- 9 -->
<section class="post col-a row-5">
  <svg class="shape" viewBox="0 0 494 617"><polygon points="322,182 494,142 494,470 322,617" fill="#a3cc7f"/></svg>
  <div class="pct-group green-txt" style="left:16px;top:34px">
    <span class="cond pct-num" style="font-size:124px;font-weight:600">25</span>
    <span class="pct-stack" style="margin-left:2px">
      <span class="cond" style="font-size:58px;font-weight:500">%</span>
      <span class="cond" style="font-size:42px;font-weight:500">OFF</span>
    </span>
  </div>
  <div class="anton forest-txt pct" style="right:22px;top:38px;font-size:48px;text-align:center;line-height:1.05">MOTHER’S DAY<br>SALE</div>
  <div class="anton forest-txt pct" style="left:28px;top:196px;font-size:122px">DETOX</div>
  <div class="anton green-txt pct" style="left:30px;top:310px;font-size:44px">THIS</div>
  <div class="anton forest-txt pct" style="left:26px;top:340px;font-size:114px">SPRING</div>
  <div class="vertical anton white-txt" style="left:338px;top:220px;font-size:108px">SHINE</div>
  <div class="vertical anton forest-txt" style="left:444px;top:214px;font-size:48px">THIS SUMMER</div>
  <div class="bottles" role="img" aria-label="Four supplement bottles" style="left:27px;top:469px;width:291px;height:142px"></div>
</section>

<!-- 10 -->
<section class="post col-b row-5">
  <svg class="shape" viewBox="0 0 494 617">
    <polygon points="465,416 494,372 494,560 465,520" fill="#d46ea2"/>
  </svg>
  <div class="t anton rose-txt" style="top:14px;font-size:132px">25%OFF</div>
  <div class="t anton plum-txt" style="top:150px;font-size:58px">MOTHER’S DAY SALE</div>
  <div class="bottles" role="img" aria-label="Four supplement bottles" style="left:70px;top:247px;width:360px;height:156px"></div>
  <div style="position:absolute;left:19px;top:416px;width:446px;height:108px;background:var(--plum)"></div>
  <div class="t anton white-txt" style="top:418px;left:19px;right:29px;font-size:86px">SPRING DETOX</div>
  <div class="t anton rose-txt" style="top:526px;font-size:54px">FOR A SUMMER BODY</div>
</section>

</main>
</body>
</html>
```